Company director needs a business card design

I am a semi-retired former senior finance executive who sits on a number of public and private company boards and do some consulting work. I work largely with emerging businesses but deal regularly with top end of town lawyers, bankers etc. I need a thoughtful but relatively conservative design which would also resonate with my younger client base. Some colour would be good. Information limited to name, address, office tel, mobile and email.

Finance

```html
<!DOCTYPE html>
<html lang="en">
<head>
<meta charset="utf-8">
<title>Business Card</title>
<link rel="stylesheet" href="https://fonts.googleapis.com/css2?family=Cinzel:wght@400;500&family=Arimo:wght@400&display=swap">
<style>
  :root {
    --page-bg: #e6e6e8;
    --card-black: #000000;
    --accent-blue: #4fa3dc;
    --text-white: #ffffff;
  }
  html, body {
    margin: 0;
    padding: 0;
    width: 1200px;
    height: 864px;
    overflow: hidden;
    background: var(--page-bg);
  }
  .canvas {
    position: relative;
    width: 1200px;
    height: 864px;
  }
  .card {
    position: absolute;
    left: 75px;
    top: 132px;
    width: 1050px;
    height: 600px;
    background: var(--card-black);
    overflow: hidden;
    box-shadow: 0 18px 40px rgba(0,0,0,0.25);
  }
  .card-shapes {
    position: absolute;
    inset: 0;
  }
  .holder-name {
    position: absolute;
    left: 78px;
    top: 318px;
    margin: 0;
    font-family: "Cinzel", "Times New Roman", serif;
    font-weight: 400;
    font-size: 44px;
    letter-spacing: 1px;
    color: var(--text-white);
  }
  .divider {
    position: absolute;
    left: 418px;
    top: 160px;
    width: 5px;
    height: 318px;
    background: var(--accent-blue);
  }
  .contact-icons {
    position: absolute;
    left: 495px;
    top: 0;
    width: 40px;
    height: 600px;
  }
  .contact-list {
    position: absolute;
    left: 585px;
    top: 182px;
    margin: 0;
    padding: 0;
    list-style: none;
    font-family: "Arimo", Arial, sans-serif;
    font-size: 29px;
    line-height: 40px;
    color: var(--text-white);
  }
  .contact-list .indent { padding-left: 14px; }
  .contact-list .gap { margin-top: 8px; }
</style>
</head>
<body>
<div class="canvas">
  <div class="card">
    <svg class="card-shapes" width="1050" height="600" viewBox="0 0 1050 600" aria-hidden="true">
      <polygon fill="var(--accent-blue)" points="0,0 1050,0 1050,85 370,85 290,25 215,105 0,105"/>
      <polygon fill="var(--accent-blue)" points="170,600 330,508 470,565 560,600"/>
    </svg>

    <p class="holder-name">Your Name</p>
    <div class="divider"></div>

    <svg class="contact-icons" width="40" height="600" viewBox="0 0 40 600" aria-hidden="true" fill="var(--text-white)">
      <path class="icon-phone" d="M11 190c-2 2-3 5-1 9 3 7 8 13 14 16 4 2 6 1 8-1l2-3-6-5-3 3c-3-1-7-6-8-9l3-3-5-7z"/>
      <g class="icon-mobile">
        <rect x="13" y="231" width="14" height="23" rx="2" fill="none" stroke="var(--text-white)" stroke-width="2.5"/>
        <rect x="17" y="249" width="6" height="2"/>
      </g>
      <path class="icon-pin" d="M20 278c-6 0-11 5-11 10 0 7 11 20 11 20s11-13 11-20c0-5-5-10-11-10zm0 14a4 4 0 1 1 0-8 4 4 0 0 1 0 8z"/>
      <g class="icon-mail" fill="none" stroke="var(--text-white)" stroke-width="2">
        <rect x="9" y="403" width="22" height="14"/>
        <path d="M9 403l11 8 11-8"/>
      </g>
    </svg>

    <ul class="contact-list">
      <li>+1 (555) 0142 376</li>
      <li>+1 (555) 0198 254</li>
      <li class="gap">48 Harbour Lane, Millbrook,</li>
      <li class="indent">NY 10482</li>
      <li class="indent">P.O. Box: 540712</li>
      <li class="indent">desk@ardenfield.net</li>
    </ul>
  </div>
</div>
</body>
</html>
```